Website front end design for an education nonprofit

This project involves design and development of the website front end (i.e., Web user interface and user experience design) for TAVO Sphere, a nonprofit initiative for developing an online platform for basic English language instruction, especially targeted toward underprivileged, non-native English speaking populations.

More about us: We are a team of educators, researchers and engineers passionate about this cause and would like to invite talented, creative web developers to join us in this effort to create positive social impact! Please send a personal message to the project owner for the executive summary to get more information about our initiative, big picture vision and the team.

TAVO Sphere website front end (UI/UX) design
Our key goals for this project are to develop an impressive Drupal-based front end for our website as well as to find really talented and creative web/UI/UX designers-cum-developers who are experts in the state-of-the-art web technologies, and are passionate about the cause of global online basic education. At the end of this project, we hope to have long term engagement with the selected developer(s) for our future website design and development needs.

Here are some preliminary guidelines on the TAVO Sphere website front end framework as envisioned by us so far. Please note that we would very much encourage creative ideas and mock-ups from the developers.

1. Current platform: Our website prototype back-end uses Drupal CMS (we plan to continue using Drupal CMS) and at the moment, a toy front-end is based on the Drupal Skeleton platform for its simplicity, clean UI and mobile device friendliness. The web developer / designer can choose any Drupal front end as a starting point or come up with a new Drupal template that meets our requirements below. Prior experience and expertise on Drupal would be great.

2. Audience profile: While the primary audience for the website is expected to be young kids (6-10 years) not very familiar with English, the secondary audience also includes adults interested in basic English language skills. So the overall goal is to have simple, uncluttered / clean, elegant and lightweight (think loading time as well as mobile device friendliness) interface that is extremely intuitive and easy to navigate, is artistic and aesthetically appealing to a wide audience (especially the non-native English speaking populations). The most important point is that our target audience should feel welcome with the clean, crisp look and easy, user-centric navigation, and should in no case feel overwhelmed (say with too much text or clutter on the front page).

3. Front page: Here is a currently envisioned preliminary sketch of the website front page (very much open for refinement and improvements)
a. The top “menu bar” part of the landing page will have our organization name and logo along with (or above) the top menu bar with the following links and sub-links
i. “Learn” link with sub-menu of all our content sections (World learning, Basic sentence learning, Classic short stories, Picture Dictionary)
ii. “About” links with information about us (sub-menu entries: About TAVO Sphere, Team, Supporters, Contributors)
iii. “Contribute” link with sub-menu entries Donate, Volunteer
iv. Menu entries towards the right side: “Login / sign up” followed by
v. “Search” with space to enter the search phrase
b. The middle “main page content” part of the page is where we would have entry points to our main content categories. The portion is envisioned to be graphical, with big blocks (images) as links to our content categories. The current categories (to start with) include 1. Word learning, 2. Basic sentence learning, and 3. Classic stories. We welcome creative ideas to represent these content categories in an appealing and elegant way (for example, these content categories could be portrayed as closed double doors that lead to the pages with the content. We would like to have placeholders for appropriate image links to different content categories – we should be able to put appropriate images or change them as we come up with new ideas that would work best with our target audience). The categories would change and grow as our content evolves, hence the core idea is to build a flexible framework that readily allows for expansion as well as customization.
c. The bottom menu / links bar portion of the landing page will have a list of links that are not included at the top. Examples include (with flexibility needed to add more when needed)
i. “Help”: this leads to a new page with FAQ, How to use
ii. “Contact us” link to a web contact form page
iii. “For Teachers” link to a page with information such as how to use, tips, pilot programs,
iv. “Volunteer” link to page with links such as Donate, Volunteer
v. “Contributors” that would link to a page with information about our Artists, Teachers, Writers, Developers etc.
vi. “Jobs” would link to a jobs page
vii. “Blog” would lead to our blog page
viii. “User stories” link to pages with feedback that we obtain from the users about how the content has helped them,
ix. Web 2.0 placeholders for social media (to be added later)

d. The footer of the website should include text “2013 TAVO Sphere, All rights reserved.”

4. The middle block of the front page is the largest in screen real estate and perhaps the most challenging part that requires much creativity and thought on the UI/UX design aspect – the content pages pointed to by the section links on the middle portion of the front page are also being designed.

5. Color preference is towards soft, elegant (think grays, whites, light blues, other light colors) web safe colors. No harsh (too bright, garish) colors.

6. Fonts preference Nice, clean looking fonts (Arial alright) compatible across browsers.

7. Portability and robustness of the front page layout for different platforms should be carefully considered. Although our first launch target platform is PC (where cross browser compatibility is important), this would very soon be followed by mobile devices such as tablets and smartphones given their prevalence across the globe. This mobile friendly design or easy portability to mobile platforms with little work requirement should be considered as a design requirement.

8. Front page as a framework for the complete website: Note that the top and the bottom portions of the front page are envisioned be used as a common template / frame across all the pages of our website – the middle portion would be used to show our content on the other pages of our website.

9. UX: For the UI/UX design, it is critical to keep in mind key qualities such as ease of use, simplicity, elegance and artistic appeal. Some specific points to keep in mind: (1) the major portion of the target audience would be new to English and (2) young children are expected to be the primary audience but we want the website to appeal to adults interested in learning as well, and (3) we need the website to work even with relatively slow Internet speeds (for underdeveloped / developing regions especially), should always be kept in mind. HTML5 compliance ideas are encouraged.

10. Strictly not desired: Typical corporate feel seen in many webpages, blocky graphics, dull and uninviting overall look with no personality, Flash type effects, harsh colors.

11. Creativity and imagination necessary: We would like to reiterate that the designer/developer has complete freedom to re-imagine the front page considering the above requirements and get back with ideas for an inspiring layout that presents the content outlined above in an intuitive format, carefully considering our target audience.

A note: As a rule, we will always make sure that our developers and artists get proper credit for their work and are recognized and acknowledged by everyone visiting our website.

Expected deliverables:
Website design psd files AND coded webpage / Drupal template: the corresponding source code and all the required libraries, images etc would be required with minimal documentation / pointers on how to make changes and customizations.

Interested developers are encouraged to first send us preliminary prototype Design for the front page to get feedback on whether their approach and style is in line with our needs and preferences. We will suggest the developers to proceed further if the team thinks there is some potential for a match (of course, the final determination would be from the pool of shortlisted submissions) – otherwise, in case the team does not see potential for a match with our needs or if we have already received multiple submissions that are comparatively more closely aligned with our vision for the website, we'd prefer to be respectful of the developers’ time and effort by requesting them not to proceed further.

Please consider this effort as your contribution to an important social cause of global and accessible online education and not a commercial enterprise (our passion for making a positive impact is what is driving the TAVO Sphere nonprofit team to undertake this initiative!). We would like to invite you to join us in this effort!

Project Deadline Extended
Reason: Due to requests from interested designers, we are extending the deadline. Looking forward to receiving many other creative designs!

Please see the project brief.

Real Estate

• Please see the project brief.

```html
<!DOCTYPE html>
<html lang="en">
<head>
<meta charset="utf-8">
<title>TAVO Sphere – Learn English</title>
<link rel="stylesheet" href="https://fonts.googleapis.com/css2?family=Source+Sans+3:wght@300;400;600&display=swap">
<style>
  :root {
    --brand-blue: #3db5e6;
    --nav-top: #9fdcf7;
    --nav-bottom: #56bdf0;
    --nav-text: #1f4e6b;
    --nav-divider: #3fa6d8;
    --text-dark: #3f3f3f;
    --text-body: #6b6b6b;
    --text-muted: #8a8a8a;
    --category-top: #f2f2f2;
    --category-bottom: #d6d6d6;
    --footer-top: #7a7a7a;
    --footer-bottom: #5d5d5d;
    --footer-base: #575757;
    --footer-text: #f1f1f1;
    --footer-line: #8c8c8c;
    --button-top: #58c1f1;
    --button-bottom: #1f93d2;
    --page-bg: #ffffff;
  }
  * { box-sizing: border-box; margin: 0; padding: 0; }
  html, body { width: 914px; height: 1200px; overflow: hidden; background: var(--page-bg); }
  body { position: relative; font-family: "Source Sans 3", Arial, sans-serif; color: var(--text-body); }
  a { color: inherit; text-decoration: none; }
  .abs { position: absolute; }

  .top-strip { left: 0; top: 0; width: 914px; height: 5px; background: #e2e2e2; }

  .brand { left: 58px; top: 28px; font-size: 35px; font-weight: 600; color: var(--brand-blue); letter-spacing: 0.3px; }

  .main-nav { left: 53px; top: 83px; width: 807px; height: 41px;
    background: linear-gradient(var(--nav-top), var(--nav-bottom)); border-radius: 3px 3px 0 0; }
  .nav-item { top: 0; height: 41px; line-height: 41px; font-size: 15px; color: var(--nav-text);
    text-align: center; border-right: 1px solid var(--nav-divider); }
  .nav-item.right { border-right: none; border-left: 1px solid var(--nav-divider); font-size: 14px; }
  .search { left: 329px; top: 10px; width: 225px; height: 24px; background: #fff;
    border: 1px solid #7bc6ea; border-radius: 2px; }
  .search-field { left: 8px; top: 0; line-height: 22px; font-size: 9.5px; color: #8c8c8c; }
  .search-button { right: -1px; top: -1px; width: 24px; height: 24px; background: #263342; border-radius: 0 2px 2px 0; }

  .hero { left: 53px; top: 124px; width: 807px; height: 278px;
    background: linear-gradient(100deg, #d6e2ea 0%, #7cc4de 35%, #4cb8d6 55%, #a9cfe0 78%, #e4ecf0 100%); }

  .categories { left: 53px; top: 402px; width: 807px; height: 65px;
    background: linear-gradient(var(--category-top), var(--category-bottom));
    border: 1px solid #cfcfcf; border-top: none; border-radius: 0 0 3px 3px; }
  .category { top: 0; height: 65px; text-align: center; border-right: 1px solid #b9b9b9; }
  .category:last-child { border-right: none; }
  .category h3 { margin-top: 14px; font-size: 19px; font-weight: 400; color: var(--text-dark); }
  .category p { font-size: 10.5px; font-weight: 300; color: var(--text-muted); margin-top: 2px; }
  .pointer { left: 454px; top: 393px; width: 0; height: 0; border-left: 9px solid transparent;
    border-right: 9px solid transparent; border-bottom: 9px solid var(--category-top); }

  .welcome-title { left: 58px; top: 508px; font-size: 21px; font-weight: 400; color: var(--brand-blue); }
  .welcome-text { left: 59px; width: 510px; font-size: 10.4px; font-weight: 300; line-height: 17.6px; color: var(--text-body); }

  .feature-image { top: 642px; width: 244px; height: 96px; }
  .feature-title { top: 744px; font-size: 15px; font-weight: 400; color: var(--text-dark); }
  .feature-text { top: 769px; width: 245px; font-size: 10.4px; font-weight: 300; line-height: 17.4px; }
  .learn-button { top: 830px; width: 81px; height: 26px; line-height: 26px; text-align: center;
    font-size: 9px; color: #fff; border-radius: 2px; background: linear-gradient(var(--button-top), var(--button-bottom));
    border: 1px solid #1a83be; }

  .sidebar { left: 596px; top: 496px; width: 318px; height: 392px;
    background: linear-gradient(90deg, #f3f3f3 0%, #ffffff 14px); }
  .sidebar-title { left: 621px; top: 512px; font-size: 18px; font-weight: 300; color: var(--text-dark); }
  .post-thumb { left: 622px; width: 82px; height: 69px; border: 3px solid #fff; box-shadow: 0 0 3px rgba(0,0,0,0.25); }
  .post-title { left: 715px; font-size: 12px; color: var(--brand-blue); }
  .post-text { left: 715px; width: 150px; font-size: 10.4px; font-weight: 300; line-height: 17.4px; }

  .footer { left: 0; top: 930px; width: 914px; height: 226px;
    border-top: 5px solid #e6e6e6; background: linear-gradient(var(--footer-top), var(--footer-bottom)); }
  .footer-heading { font-size: 16.5px; font-weight: 400; color: var(--footer-text); }
  .footer-links { list-style: none; font-size: 10.6px; font-weight: 400; color: var(--footer-text); }
  .footer-links li { height: 20.5px; }
  .footer-divider { top: 46px; width: 1px; height: 138px; background: var(--footer-line); }
  .newsletter-note { font-size: 10.6px; color: var(--footer-text); }
  .email-field { left: 343px; top: 89px; width: 199px; height: 23px; background: #f4f4f4;
    border-radius: 2px; font-size: 9.5px; line-height: 23px; padding-left: 10px; color: #8a8a8a; }
  .subscribe-button { left: 454px; top: 119px; width: 91px; height: 28px; line-height: 27px; text-align: center;
    font-size: 13px; color: #15476a; border-radius: 2px; background: linear-gradient(#8ad8fb, #3bb3ec); }
  .social { top: 78px; width: 24px; height: 24px; border-radius: 50%; background: #f2f2f2; }

  .base-bar { left: 0; top: 1156px; width: 914px; height: 44px; background: var(--footer-base); }
  .copyright { left: 65px; top: 15px; font-size: 10.5px; color: #a9a9a9; }
</style>
</head>
<body>
  <div class="abs top-strip"></div>

  <header>
    <a class="abs brand" href="#">TAVO Sphere</a>
    <nav class="abs main-nav">
      <a class="abs nav-item" href="#" style="left:0;width:94px;">Learn</a>
      <a class="abs nav-item" href="#" style="left:94px;width:88px;">About</a>
      <a class="abs nav-item" href="#" style="left:182px;width:113px;border-right:none;">Contribute</a>
      <div class="abs search">
        <span class="abs search-field">type your word</span>
        <span class="abs search-button">
          <svg width="24" height="24" viewBox="0 0 24 24"><circle cx="11" cy="11" r="4.2" fill="none" stroke="#fff" stroke-width="1.6"/><line x1="14" y1="14" x2="17" y2="17" stroke="#fff" stroke-width="1.8" stroke-linecap="round"/></svg>
        </span>
      </div>
      <a class="abs nav-item right" href="#" style="left:673px;width:70px;">Sign Up</a>
      <a class="abs nav-item right" href="#" style="left:743px;width:64px;">Log In</a>
    </nav>
  </header>

  <main>
    <div class="abs hero" role="img" aria-label="Photo of smiling children in a classroom gathered around a globe"></div>
    <div class="abs pointer"></div>
    <div class="abs categories">
      <a class="abs category" href="#" style="left:0;width:269px;"><h3>Word Learning</h3><p>Duis tincidunt lectus quis dui viverra stibulum</p></a>
      <a class="abs category" href="#" style="left:269px;width:269px;"><h3>Basic Sentence Learning</h3><p>Duis tincidunt lectus quis dui viverra stibulum</p></a>
      <a class="abs category" href="#" style="left:538px;width:268px;"><h3>Classic Stories</h3><p>Duis tincidunt lectus quis dui viverra stibulum</p></a>
    </div>

    <h1 class="abs welcome-title">Welcome to Our Website Mainpage</h1>
    <p class="abs welcome-text" style="top:539px;">Nunc tempus felis vitae urna. Vivamus porttitor, g, purus nisi eleifend libero, a tempus libero lectus feugiat felis. Morbi diam mauris, viverra in, gravida eu, mattis in, ante. Morbi eget arcu.</p>
    <p class="abs welcome-text" style="top:580px;">Morbi porta, libero id ullamcorper nonummy, nibh ligula pulvinar metus, eget consectetuer augue nisi quis lacus. Ut ac mi quis lacus mollis aliquam. Curabitur iaculis tempus eros. Curabitur vel mi sit amet magna malesuada</p>

    <section>
      <div class="abs feature-image" style="left:58px;background:linear-gradient(90deg,#8fa4c0,#c9b6a8 45%,#d8d2c6);" role="img" aria-label="Photo of students listening attentively in class"></div>
      <h2 class="abs feature-title" style="left:58px;">Why Contribute Us</h2>
      <p class="abs feature-text" style="left:58px;">Phasellus felis dolor, scelerisque a, tempus eget, lobortis id, libero. Donec scelerisque leo ac risus. Praesent sit amet est. In dictum</p>
      <a class="abs learn-button" href="#" style="left:58px;">LEARN MORE</a>

      <div class="abs feature-image" style="left:319px;background:linear-gradient(90deg,#5a4a3a,#8a7058 40%,#a09080 60%,#6b5642);" role="img" aria-label="Photo of a smiling student in a library"></div>
      <h2 class="abs feature-title" style="left:320px;">How We Works</h2>
      <p class="abs feature-text" style="left:320px;">Phasellus felis dolor, scelerisque a, tempus eget, lobortis id, libero. Donec scelerisque leo ac risus. Praesent sit amet est. In dictum</p>
      <a class="abs learn-button" href="#" style="left:321px;">LEARN MORE</a>
    </section>

    <aside>
      <div class="abs sidebar"></div>
      <h2 class="abs sidebar-title">Recent Blog Post</h2>

      <div class="abs post-thumb" style="top:549px;background:linear-gradient(135deg,#6b4a3a,#c9a08a 55%,#e6a0c0);" role="img" aria-label="Photo of a parent reading with a child"></div>
      <a class="abs post-title" href="#" style="top:548px;">Curabitur iaculis</a>
      <p class="abs post-text" style="top:567px;">Vivamus porttitor, g, purus nisi eleifend libero, a tempus libero lectus feugiat felis</p>

      <div class="abs post-thumb" style="top:647px;background:linear-gradient(135deg,#eef0f2,#dadde0 50%,#4a3a32 70%,#d8c8b8);" role="img" aria-label="Photo of a child writing on a whiteboard"></div>
      <a class="abs post-title" href="#" style="top:646px;">Donec scelerisque</a>
      <p class="abs post-text" style="top:665px;">Vivamus porttitor, g, purus nisi eleifend libero, a tempus libero lectus feugiat felis</p>

      <div class="abs post-thumb" style="top:746px;background:linear-gradient(135deg,#6b9a5a,#d8c0b0 45%,#4a7ec0 75%,#c05050);" role="img" aria-label="Photo of a teacher and student reading a book"></div>
      <a class="abs post-title" href="#" style="top:745px;">Suspendisse quam leo</a>
      <p class="abs post-text" style="top:764px;">Vivamus porttitor, g, purus nisi eleifend libero, a tempus libero lectus feugiat felis</p>
    </aside>
  </main>

  <footer class="abs footer">
    <h3 class="abs footer-heading" style="left:72px;top:42px;">Quick Links</h3>
    <ul class="abs footer-links" style="left:75px;top:72px;">
      <li>Help</li><li>Contact us</li><li>For teachers</li><li>Volunteer</li><li>Contributors</li><li>Jobs</li>
    </ul>
    <h3 class="abs footer-heading" style="left:205px;top:43px;">Sub Links</h3>
    <ul class="abs footer-links" style="left:207px;top:72px;">
      <li>Blog</li><li>User stories</li><li>Support</li><li>Term of Use</li><li>FAQ</li>
    </ul>
    <div class="abs footer-divider" style="left:307px;"></div>

    <h3 class="abs footer-heading" style="left:343px;top:42px;">Subscribe Newsletters</h3>
    <p class="abs newsletter-note" style="left:343px;top:69px;">Please subscribe here for latest news &amp; offers.</p>
    <div class="abs email-field">email address</div>
    <a class="abs subscribe-button" href="#">Subscribe</a>
    <div class="abs footer-divider" style="left:583px;"></div>

    <h3 class="abs footer-heading" style="left:618px;top:42px;">Get Connted With Us</h3>
    <span class="abs social" style="left:616px;"></span>
    <span class="abs social" style="left:644px;"></span>
    <span class="abs social" style="left:672px;"></span>
    <span class="abs social" style="left:700px;"></span>
  </footer>

  <div class="abs base-bar">
    <p class="abs copyright">2013 TAVO Sphere, All rights reserved</p>
  </div>
</body>
</html>
```